BWP Business Card

A double sided business card based on your "Brindlewood Partners Ltd" Logo. To use the "BWP" logo on 1 side and the full company logo on the reverse.

Detials to be included:

Name: Tomas Wheeler
Postion: Consultant Orthotist & Expert Witness
T: +44 (0) 7700 938271
F: +44 (0) 7654 8820

```html
<!DOCTYPE html>
<html lang="en">
<head>
<meta charset="utf-8">
<title>BWP Business Card</title>
<link rel="stylesheet" href="https://fonts.googleapis.com/css2?family=Tinos:wght@400;700&display=swap">
<style>
  :root {
    --navy: #0b3a70;
    --grey: #9a9a9a;
    --ink: #2a2a2a;
    --paper: #ffffff;
    --backdrop: #e4e4ea;
  }
  * { margin: 0; padding: 0; box-sizing: border-box; }
  html, body { width: 1200px; height: 987px; overflow: hidden; }
  body {
    background: var(--backdrop);
    font-family: "Tinos", "Times New Roman", serif;
    position: relative;
  }
  .card {
    position: absolute;
    width: 640px;
    height: 410px;
    background: var(--paper);
    border-radius: 34px;
    overflow: hidden;
    box-shadow: 0 6px 18px rgba(0,0,0,0.12);
  }
  .card--front { left: 70px; top: 60px; }
  .card--back { left: 490px; top: 517px; }

  /* Front */
  .front-mark {
    position: absolute;
    left: 50px; top: 60px;
    display: flex; align-items: center; gap: 14px;
  }
  .front-mark__square { width: 26px; height: 26px; background: var(--navy); }
  .front-mark__name {
    font-size: 64px; font-weight: 700; color: var(--navy);
    letter-spacing: 4px; line-height: 1;
  }
  .front-divider {
    position: absolute; left: 300px; top: 50px;
    width: 1px; height: 200px; background: var(--grey);
  }
  .contact { position: absolute; left: 325px; top: 52px; color: var(--ink); }
  .contact__name { font-size: 24px; font-weight: 700; color: var(--navy); }
  .contact__role { font-size: 16px; color: var(--grey); margin-bottom: 10px; }
  .contact__address { font-size: 17px; line-height: 1.25; margin-bottom: 12px; }
  .contact__line { display: flex; align-items: center; gap: 8px; font-size: 17px; line-height: 1.5; }
  .contact__icon { width: 16px; height: 16px; flex: none; }
  .front-waves { position: absolute; left: 0; bottom: 0; width: 640px; height: 250px; }

  /* Back */
  .back-lockup {
    position: absolute; left: 60px; top: 120px;
    display: flex; align-items: center; gap: 26px;
  }
  .back-lockup__square { width: 70px; height: 70px; background: var(--navy); flex: none; }
  .back-lockup__divider { width: 1px; height: 130px; background: var(--grey); }
  .back-lockup__name {
    font-size: 40px; font-weight: 700; color: var(--navy);
    line-height: 1.05; letter-spacing: 1px; text-transform: uppercase;
  }
  .back-lockup__tagline {
    margin-top: 8px; padding-top: 5px;
    border-top: 1px solid var(--grey);
    font-size: 13px; font-weight: 700; color: var(--ink);
    letter-spacing: 1px; text-transform: uppercase;
  }
</style>
</head>
<body>

<section class="card card--front" aria-label="Business card front">
  <svg class="front-waves" viewBox="0 0 640 250" aria-hidden="true">
    <path d="M0 55 C150 45 260 120 330 250 L0 250 Z" fill="var(--grey)"/>
    <path d="M0 75 C160 70 270 150 340 250 L0 250 Z" fill="var(--paper)"/>
    <path d="M0 85 C170 80 280 160 350 250 L0 250 Z" fill="var(--navy)"/>
    <path d="M220 90 C300 150 420 220 640 235 L640 250 L330 250 C300 190 270 140 220 90 Z" fill="var(--grey)"/>
    <path d="M232 105 C310 165 430 225 640 240 L640 250 L345 250 C315 195 285 150 232 105 Z" fill="var(--paper)"/>
    <path d="M0 95 C175 92 285 170 352 250 L0 250 Z" fill="var(--navy)"/>
  </svg>

  <div class="front-mark">
    <span class="front-mark__square"></span>
    <span class="front-mark__name">BWP</span>
  </div>

  <div class="front-divider"></div>

  <div class="contact">
    <p class="contact__name">Tomas Wheeler</p>
    <p class="contact__role">Consultant Orthotist &amp; Expert Witness</p>
    <p class="contact__address">18 Harlow Lane Kingsford<br>Surrey, KT9 4PD</p>
    <p class="contact__line">
      <svg class="contact__icon" viewBox="0 0 16 16" aria-hidden="true"><circle cx="8" cy="8" r="8" fill="var(--navy)"/><path d="M5 4 L7 6 L6 7 C6.5 8.5 7.5 9.5 9 10 L10 9 L12 11 L10.5 12.5 C7 12 4 9 3.5 5.5 Z" fill="#fff"/></svg>
      +44 (0) 7700 938271
    </p>
    <p class="contact__line">
      <svg class="contact__icon" viewBox="0 0 16 16" aria-hidden="true"><circle cx="8" cy="8" r="8" fill="var(--navy)"/><rect x="5" y="3.5" width="6" height="3" fill="#fff"/><rect x="3.5" y="6.5" width="9" height="4" fill="#fff"/><rect x="5" y="10" width="6" height="2.5" fill="#fff"/></svg>
      +44 (0) 7654 8820
    </p>
    <p class="contact__line">
      <svg class="contact__icon" viewBox="0 0 16 16" aria-hidden="true"><circle cx="8" cy="8" r="8" fill="var(--navy)"/><rect x="3.5" y="5" width="9" height="6" fill="#fff"/><path d="M3.5 5 L8 8.5 L12.5 5" fill="none" stroke="var(--navy)" stroke-width="1"/></svg>
      tomas@brindlewoodpartners.co.uk
    </p>
  </div>
</section>

<section class="card card--back" aria-label="Business card back">
  <div class="back-lockup">
    <span class="back-lockup__square"></span>
    <span class="back-lockup__divider"></span>
    <div>
      <p class="back-lockup__name">Brindlewood<br>Partners Ltd</p>
      <p class="back-lockup__tagline">Excellence in Medical Legal Reporting</p>
    </div>
  </div>
</section>

</body>
</html>
```